A unique communication angle to crowdfunding

Looking for a fresh redesign of a crowd funding website that deals in real estate. I already have the content, but am looking to take the design to the next level.

Existing real estate crowd funding sites focus on the real estate. I want to explore communication angle that:
- puts the investor in the centre of the communication: "become a baron"
- highlights the international nature (international properties, international investors)

There's also quite a lot of copy on the site, as we need to explain the service in quite a bit of detail. There's room to reduce the copy and replace with graphics. Could also consider clicking to see different text (see our difference section in http://galleonfairs.com)

The backend of the platform is already being worked on by a specialist crowd funding service provider.

In total there are 5 pages to be designed.

The homepage is really important. Right now it looks quite dated. It doesn't have a great layout. Note there is no mobile version of the website, so the pages need to be seen well on mobile devices. When looking at the brief, refer to the following links too:

current website:
http://pennyduke.com

some revisions made so far:
http://preview.stakeharbor.com/7K3LQ9

Attached are logo files and another file which contained copy for the pages. No need to rework the logo.

Please make sure to use the same copy in the brief on the webpages, to ensure the layouts work. Designers are free to propose images they feel work on the pages.

I would like to see if rather than tweaking the pages, it's possible to come up with a better design concept. If the 5 pages are accepted, there's a chance I'll request an additional 4 pages.
Updates

Please note the font used in the logo is called "harabara" in case you decide to use it in any of the titles, etc.

Please note there is one additional page for which we would like to review designs. Note the page would be a template to be used on all future real estate detail pages. Here is an example of the current design for reference:

http://pennyduke.com/projects/view/14

In total there are 5 page designs required, (homepage + 4)

Thank you

FYI -

Just a quick note to give information from similar UK real estate crowdfunding sites:
http://www.housewalrus.co.uk
http://tiderock.co.uk
https://www.fundquarry.com

Of the above, only tiderock has a nice clean looking landing page. Information is clear and well laid out.

Hi all, just uploaded a new file in the brief. Contains some comments and a website reference. I thought it may help to explain how we could convey international aspect as well as how we could convey images in a more modern way. This is an option you can consider, but its entirely up to you how how answer the brief. Thanks!

Reason: As requested by some designers needing more time to complete their work. Continue to share your work in progress and receive timely feedback before the deadline.

We would like to let you know that we have just shortlisted the best designs. Together with that, we have also passed some detailed feedback to all designers who weren't shortlisted. If we didn't contact you, please let us know. If you haven't submitted a design or are working on revisions, please note these will no longer be taken into account now. We hope you understand that we need to close the project today. Thank you all once again for your great work and design concepts. Here's hoping we meet again on a future design brief. Cheers, pennyduke team.

Target Market(s)

At the moment, only rich are able to buy real estate. With this service, anyone can become a landlord. Target buyers:

Young professionals, looking to diversify from stock market and lower risk
People nearing retirement, looking for stable rental incomes
Retirees - looking to supplement pensions with possibility of capital gains
Parents - looking for a way to save long term for their children (instead of low interest paying bank accounts)

Industry/Entity Type

Communication

Font styles to use
Sans Serif
Other font styles liked:
• harabara

Colors
add136
f5f9eb
959595
000000

Requirements
Must have
• Overall, the site must convey "whoever you are, you too can become a landlord", and that you don't need to be wealthy to invest in real estate. See

Communication should put the investor (or the baron) at the centre. The investor can be any of those described in the target market.

Show the aspirational side of property ownership.

In addition to the investor/baron character, the second main theme is international. No other real estate crowdfunding website highlights this.
Nice to have
• Banner could show different consumer types, to illustrate that the service can appeal to many different profiles. Refer to attached file "home page reference - plainasbread.com" as an example of how this could be done.

Aim to show the international side of the service. Properties around the world, investors around the world.

```html
<!DOCTYPE html>
<html lang="en">
<head>
<meta charset="utf-8">
<title>pennyduke – Become a Baron</title>
<link href="https://fonts.googleapis.com/css2?family=Open+Sans:wght@300;400;600;700&display=swap" rel="stylesheet">
<style>
:root{
  --green:#add136;
  --green-dark:#8fb321;
  --green-tint:#eef4d4;
  --cream:#f5f9eb;
  --hero:#fbfcee;
  --grey:#959595;
  --grey-light:#e6e6e6;
  --text:#555;
  --muted:#777;
  --ink:#222;
  --footer:#1f1f1f;
  --white:#fff;
}
*{box-sizing:border-box;margin:0;padding:0}
html,body{width:1200px;height:3130px;overflow:hidden}
body{font-family:"Open Sans",Arial,sans-serif;color:var(--text);background:var(--white);position:relative}
section,header,footer{position:absolute;left:0;width:1200px}

/* header */
.site-header{top:0;height:146px;border-bottom:2px solid #ddd;background:var(--white)}
.brand{position:absolute;left:100px;top:48px;display:flex;align-items:center;gap:12px}
.brand-mark{width:44px;height:44px;border-radius:50%;background:var(--green)}
.brand-name{font-size:32px;font-weight:700;color:var(--green);letter-spacing:-.5px}
.social{position:absolute;left:752px;top:44px;display:flex;gap:10px}
.social span{width:26px;height:26px;border-radius:50%;background:var(--green);display:block}
.search{position:absolute;left:902px;top:41px;width:197px;height:32px;border:1px solid #ccc;border-radius:3px;font-size:13px;color:#aaa;padding:6px 14px}
.search svg{position:absolute;right:8px;top:6px}
.main-nav{position:absolute;right:100px;top:112px;display:flex}
.main-nav a{font-size:13px;color:#444;text-decoration:none;padding:4px 0 12px;margin-left:38px;border-bottom:3px solid transparent}
.main-nav a.active{color:var(--green);border-bottom-color:var(--green)}

/* hero */
.hero{top:147px;height:500px;background:var(--hero)}
.hero h1{position:absolute;left:140px;width:920px;top:42px;text-align:center;font-weight:300;font-size:32px;line-height:44px;color:var(--muted)}
.hero-art{position:absolute;left:0;top:248px;width:1200px;height:252px;background:linear-gradient(90deg,#d5d9dc 0%,#6c8fb8 25%,#3d6fa8 50%,#7fa9d8 75%,#d3d8dc 100%)}
.hero-arrow{position:absolute;top:240px;width:38px;height:38px;border-radius:50%;background:#ccc;display:flex;align-items:center;justify-content:center;z-index:1}
.hero-arrow.prev{left:30px}.hero-arrow.next{right:30px}

/* intro */
.intro{top:647px;height:240px;text-align:center}
.intro h2{margin-top:50px;font-size:28px;font-weight:400;color:var(--green)}
.intro p{width:880px;margin:16px auto 0;font-size:14.5px;line-height:24px;color:var(--muted)}
.intro p + p{margin-top:14px}

/* split */
.split{top:887px;height:305px;display:flex}
.split-panel{width:600px;height:305px;position:relative;color:var(--white)}
.split-panel.members{background:var(--green)}
.split-panel.buyers{background:var(--ink)}
.members h3,.members p,.members .btn{left:110px}
.buyers h3,.buyers p,.buyers .btn{left:32px}
.split-panel h3{position:absolute;top:95px;font-size:40px;font-weight:700}
.split-panel p{position:absolute;top:152px;font-size:17px;line-height:24px;font-weight:600;width:450px}
.split-panel p small{display:block;font-size:15px;font-weight:600}
.split-panel .icon{position:absolute;top:30px;width:96px;height:90px;border-radius:6px}
.members .icon{right:34px;background:#2e3a10}
.buyers .icon{left:352px;width:140px;background:#eee;border-radius:45px 45px 12px 12px}
.btn{position:absolute;top:228px;height:46px;padding:0 18px;border-radius:3px;font-size:17px;font-weight:600;line-height:46px}
.members .btn{background:#333;color:var(--white)}
.buyers .btn{background:var(--green);color:var(--ink);border:1px solid var(--green-dark)}

/* featured */
.featured{top:1192px;height:686px;text-align:center}
.featured h2{margin-top:56px;font-size:28px;font-weight:400;color:var(--green)}
.featured .lead{width:600px;margin:14px auto 0;font-size:14.5px;line-height:24px;color:var(--muted)}
.cards{position:absolute;top:190px;left:100px;display:flex;gap:32px}
.card{width:313px;height:407px;border:1px solid #ddd;background:var(--white);position:relative}
.card-price{height:50px;background:var(--green);color:var(--white);font-size:21px;font-weight:600;line-height:50px}
.card-photo{height:146px}
.card h4{margin-top:20px;font-size:18px;font-weight:400;color:var(--green)}
.card-text{width:240px;margin:8px auto 0;font-size:11px;line-height:16px;color:#888}
.progress{position:absolute;left:20px;right:20px;top:322px;height:8px;background:#e8e8e8;border-radius:4px}
.progress i{display:block;height:8px;background:var(--green);border-radius:4px}
.funded{position:absolute;left:20px;top:338px;font-size:13px;color:var(--text)}
.card .view{position:absolute;left:85px;top:382px;width:143px;height:42px;background:#333;color:var(--white);font-size:17px;line-height:42px;border-radius:2px}

/* newsletter */
.newsletter{top:1878px;height:178px;background:var(--grey-light);text-align:center}
.newsletter h2{margin-top:24px;font-size:30px;font-weight:400;color:#333}
.newsletter p{font-size:12.5px;color:var(--text);margin-top:2px}
.signup{display:flex;justify-content:center;gap:10px;margin-top:20px}
.signup .field{width:270px;height:40px;background:var(--white);border:1px solid #ccc;text-align:left;padding:10px 12px;font-size:12.5px;color:#999}
.signup .submit{width:95px;height:40px;background:var(--text);color:var(--white);font-size:14px;font-weight:700;line-height:40px;border-radius:2px}

/* community */
.community{top:2056px;height:563px;text-align:center}
.community h2{margin-top:50px;font-size:28px;font-weight:400;color:var(--green)}
.community .lead{margin-top:12px;font-size:14.5px;color:var(--muted)}
.stats{position:absolute;top:156px;left:120px;display:flex;gap:83px}
.stat{width:264px}
.stat-box{margin:0 auto;width:207px;height:84px;background:var(--green-tint);padding-top:10px}
.stat-box b{font-size:36px;font-weight:700;color:var(--green)}
.stat-box b span{font-size:14px;font-weight:400}
.stat-box em{display:block;font-style:normal;font-size:14px;color:var(--green);margin-top:-6px}
.stat p{margin-top:12px;font-size:16px;line-height:23px;color:#333}
.press{position:absolute;left:121px;top:354px;width:958px;height:142px;border:1px solid #ccc}
.press small{position:absolute;left:16px;top:12px;font-size:11px;color:var(--text)}
.press-row{position:absolute;left:28px;display:flex;gap:22px;align-items:center}
.press-row span{display:block;background:#9a9a9a;border-radius:3px}

/* legal */
.legal{top:2619px;height:366px;background:var(--grey-light)}
.skyline{position:absolute;left:0;bottom:0;width:1200px;height:140px;background:linear-gradient(180deg,#d4d4d4,#a9a9a9)}
.legal-box{position:absolute;left:129px;width:950px;background:var(--white);padding:16px 14px 0;font-size:12.2px;line-height:20px;color:#8a8a8a}
.legal-box.one{top:31px;height:143px}
.legal-box.two{top:190px;height:145px}

/* footer */
.site-footer{top:2985px;height:145px;background:var(--footer);color:#bbb}
.footer-nav{position:absolute;left:190px;top:31px;display:flex;gap:30px;font-size:13px}
.footer-nav a{color:#bbb;text-decoration:none}
.footer-nav a::before{content:"• "}
.copyright{position:absolute;left:100px;top:98px;font-size:13px}
.footer-social{position:absolute;left:798px;top:94px;display:flex;gap:10px}
.footer-social span{width:26px;height:26px;border-radius:50%;background:#888;display:block}
.group-badge{position:absolute;left:943px;top:84px;width:158px;height:46px;background:#888}
</style>
</head>
<body>

<header class="site-header">
  <div class="brand"><span class="brand-mark"></span><span class="brand-name">pennyduke</span></div>
  <div class="social" aria-label="Social links"><span></span><span></span><span></span><span></span></div>
  <div class="search">Search
    <svg width="18" height="18" viewBox="0 0 18 18"><circle cx="7.5" cy="7.5" r="5.5" fill="none" stroke="#666" stroke-width="2"/><line x1="11.5" y1="11.5" x2="16" y2="16" stroke="#666" stroke-width="2"/></svg>
  </div>
  <nav class="main-nav">
    <a class="active" href="#">Home</a>
    <a href="#">Sign In</a>
    <a href="#">How it Works</a>
    <a href="#">Discover A Project</a>
    <a href="#">The Duke Journal</a>
    <a href="#">Find Out More</a>
  </nav>
</header>

<section class="hero">
  <h1>The pennyduke community is social and collaborative. Pool with friends. Share any gains.</h1>
  <div class="hero-arrow prev"><svg width="14" height="14" viewBox="0 0 14 14"><path d="M9 2 4 7l5 5" fill="none" stroke="#fff" stroke-width="2.5"/></svg></div>
  <div class="hero-arrow next"><svg width="14" height="14" viewBox="0 0 14 14"><path d="M5 2l5 5-5 5" fill="none" stroke="#fff" stroke-width="2.5"/></svg></div>
  <div class="hero-art" role="img" aria-label="Illustration of a crowd of business people standing before a blue city skyline with modern towers"></div>
</section>

<section class="intro">
  <h2>pennyduke is reconstructing a property ladder that's strong and fair</h2>
  <p>By harnessing the power of crowds, it's possible to become a landlord in attractive locations around the world without the burden of financing 100% of the purchase. Leave the day to day management of your property portfolio to us.</p>
  <p>Start with as little as 1% in a project and plan your steps to becoming a true baron.</p>
</section>

<section class="split">
  <div class="split-panel members">
    <div class="icon" role="img" aria-label="Apartment building icon"></div>
    <h3>Find Properties</h3>
    <p>Sign up to browse the portfolio.<small>Your journey to becoming a real estate baron starts here.</small></p>
    <div class="btn">Become a Member</div>
  </div>
  <div class="split-panel buyers">
    <div class="icon" role="img" aria-label="Group of investors icon"></div>
    <h3>Find Buyers</h3>
    <p>Submit a property or development and raise funds from our real estate barons.</p>
    <div class="btn">Submit Your Project</div>
  </div>
</section>

<section class="featured">
  <h2>Featured Projects</h2>
  <p class="lead">Brief details of new and popular projects. To view full listings, you will be required to sign up and become a member.</p>
  <div class="cards">
    <article class="card">
      <div class="card-price">From GBP 3,600</div>
      <div class="card-photo" role="img" aria-label="Photo of a waterfront city skyline" style="background:linear-gradient(180deg,#cfe3ef,#7ea8c4 60%,#2f8ab5)"></div>
      <h4>14 Harrow Quay London E9</h4>
      <p class="card-text">Class aptent taciti sociosqu ad litora torquent per conubia nostra, per inceptos himenaeos. Donec ac sem id lorem ultrices.</p>
      <div class="progress"><i style="width:0"></i></div>
      <div class="funded">0%&nbsp; funded</div>
      <div class="view">View more</div>
    </article>
    <article class="card">
      <div class="card-price">From GBP 3,600</div>
      <div class="card-photo" role="img" aria-label="Photo of a brick retail building" style="background:linear-gradient(180deg,#c9d8e8,#8a6a56 55%,#b8b4ae)"></div>
      <h4>14 Harrow Quay London E9</h4>
      <p class="card-text">Class aptent taciti sociosqu ad litora torquent per conubia nostra, per inceptos himenaeos. Donec ac sem id lorem ultrices.</p>
      <div class="progress"><i style="width:4%"></i></div>
      <div class="funded">4%&nbsp; funded</div>
      <div class="view">View more</div>
    </article>
    <article class="card">
      <div class="card-price">From GBP 3,600</div>
      <div class="card-photo" role="img" aria-label="Photo of a large Mediterranean style apartment building" style="background:linear-gradient(180deg,#8fb5d8,#b98a66 50%,#9a6a4a)"></div>
      <h4>14 Harrow Quay London E9</h4>
      <p class="card-text">Class aptent taciti sociosqu ad litora torquent per conubia nostra, per inceptos himenaeos. Donec ac sem id lorem ultrices.</p>
      <div class="progress"><i style="width:51%"></i></div>
      <div class="funded">51%&nbsp; funded</div>
      <div class="view">View more</div>
    </article>
  </div>
</section>

<section class="newsletter">
  <h2>Get In Touch</h2>
  <p>sign up to receive additional information on new projects and get the newsletter</p>
  <div class="signup"><div class="field">E-mail Address</div><div class="submit">SUBMIT</div></div>
</section>

<section class="community">
  <h2>Be Part of a Growing International Community</h2>
  <p class="lead">Gain access to new projects in world class cities and join our growing community of international landlords.</p>
  <div class="stats">
    <div class="stat"><div class="stat-box"><b>3,200 <span>investors</span></b><em>in 6 countrie</em></div><p>A community of international<br>property barons.</p></div>
    <div class="stat"><div class="stat-box"><b>2,800 <span>investors</span></b><em>in 6 countrie</em></div><p>Collective buying power of<br>the pennyduke community</p></div>
    <div class="stat"><div class="stat-box"><b>1,200 <span>investors</span></b><em>in 6 countrie</em></div><p>Attractive real estate from<br>around the world</p></div>
  </div>
  <div class="press">
    <small>Featured in</small>
    <div class="press-row" style="top:38px">
      <span style="width:120px;height:30px"></span>
      <span style="width:135px;height:22px"></span>
      <span style="width:150px;height:30px"></span>
      <span style="width:80px;height:38px"></span>
      <span style="width:46px;height:38px"></span>
      <span style="width:140px;height:26px"></span>
    </div>
    <div class="press-row" style="top:90px">
      <span style="width:50px;height:30px"></span>
      <span style="width:130px;height:30px"></span>
      <span style="width:300px;height:26px"></span>
    </div>
  </div>
</section>

<section class="legal">
  <div class="skyline" role="img" aria-label="Grey city skyline silhouette"></div>
  <div class="legal-box one"><p>By accessing this site and any pages thereof, you agree to be bound by the terms and conditions. This website is only suitable, intended and available for professional or sophisticated, or similar investors in other jurisdictions, or those who are members of pennyduke community and familiar with, and willing to, accept the risks associated with private participation. pennyduke does not endorse any of the projects that appear on this website, nor does it make any recommendations regarding the appropriateness of particular opportunities for any participant. Each potential participant must review and evaluate the projects in his or her own discretion and determine the suitability of participating.</p></div>
  <div class="legal-box two"><p>This website (the "Site") is in every respect unaffiliated with any site to which it links or to any company or entity (and connected projects, investment opportunity or similar) featured on this website, and is not meant as an endorsement of any of those companies or entities ("third parties"). Furthermore and for the avoidance of doubt, pennyduke Limited is in no way affiliated with any third parties featured or referenced on this Site. There is no commercial relationship between pennyduke Limited and such third parties, nor an agency arrangement or similar. If you believe your Content (including third party content) as each such term is defined in our Terms of Service has been reproduced on the Site with-</p></div>
</section>

<footer class="site-footer">
  <nav class="footer-nav">
    <a href="#">Terms of Service</a><a href="#">Privacy Policy</a><a href="#">How It Works</a><a href="#">Discover A Project</a><a href="#">The Duke Journal</a><a href="#">FAQ</a><a href="#">Contact</a>
  </nav>
  <div class="copyright">Copyright &nbsp;©&nbsp; 2014 &nbsp;pennyduke. &nbsp;All rights reserved.</div>
  <div class="footer-social" aria-label="Social links"><span></span><span></span><span></span><span></span></div>
  <div class="group-badge" role="img" aria-label="Parent group badge"></div>
</footer>

</body>
</html>
```